Residential & commercial landscaping company

Updated business cards for commercial and landscaping company. We would like to keep out logo, but just need a more updated business card.

```html
<!DOCTYPE html>
<html lang="en">
<head>
<meta charset="utf-8">
<title>GreenHollow Business Card</title>
<link rel="stylesheet" href="https://fonts.googleapis.com/css2?family=Arimo:wght@400;700&family=Tinos:wght@700&display=swap">
<style>
  :root {
    --page-bg: #a9a9a9;
    --card-dark: #151515;
    --card-light: #ffffff;
    --brand-green: #2fbf3a;
    --deep-green: #0c7a2f;
    --ink: #111111;
    --faint-dark: #1f1f1f;
    --faint-light: #e6e6e6;
  }
  * { box-sizing: border-box; margin: 0; padding: 0; }
  html, body {
    width: 1200px; height: 900px; overflow: hidden;
    background: var(--page-bg);
    font-family: "Arimo", Arial, sans-serif;
  }
  .canvas {
    position: relative; width: 1200px; height: 900px;
  }
  .card {
    position: absolute; left: 290px; width: 620px; height: 354px;
    border-radius: 30px; overflow: hidden;
  }
  .card--front { top: 60px; background: var(--card-dark); }
  .card--back { top: 470px; background: var(--card-light); }

  .card__texture {
    position: absolute; right: 0; top: 0; width: 300px; height: 100%;
  }
  .card--front .card__texture {
    background: radial-gradient(ellipse at 70% 50%, var(--faint-dark) 0%, var(--card-dark) 75%);
  }
  .card--back .card__texture {
    background: radial-gradient(ellipse at 65% 50%, var(--faint-light) 0%, #f2f2f2 55%, var(--card-light) 85%);
  }

  .wordmark {
    position: absolute; display: flex; align-items: center; gap: 14px;
    font-weight: 700; letter-spacing: -1px;
  }
  .wordmark__mark {
    background: var(--deep-green); flex: none;
  }
  .card--front .wordmark {
    left: 50%; top: 50%; transform: translate(-50%, -50%);
    color: #ffffff; font-size: 62px;
  }
  .card--front .wordmark__mark { width: 58px; height: 58px; }

  .card--back .wordmark {
    left: 52px; top: 46px; color: var(--ink); font-size: 46px;
  }
  .card--back .wordmark__mark { width: 44px; height: 44px; }

  .contact {
    position: absolute; left: 56px; top: 150px;
  }
  .contact__name {
    font-family: "Tinos", "Times New Roman", serif; font-weight: 700;
    color: var(--brand-green); font-size: 32px; line-height: 1;
  }
  .contact__role {
    font-size: 17px; color: var(--ink); margin-top: 4px;
  }
  .contact__list {
    list-style: none; margin-top: 22px;
  }
  .contact__item {
    display: flex; align-items: center; gap: 10px;
    font-size: 17px; color: var(--ink); line-height: 26px;
  }
  .contact__icon { width: 18px; height: 18px; flex: none; }
</style>
</head>
<body>
<main class="canvas">

  <section class="card card--front" aria-label="Card front">
    <div class="card__texture" role="img" aria-label="Faint tree canopy silhouette decoration"></div>
    <div class="wordmark">
      <span class="wordmark__mark"></span>
      <span class="wordmark__name">GreenHollow</span>
    </div>
  </section>

  <section class="card card--back" aria-label="Card back">
    <div class="card__texture" role="img" aria-label="Faint grey tree canopy silhouette decoration"></div>
    <div class="wordmark">
      <span class="wordmark__mark"></span>
      <span class="wordmark__name">GreenHollow</span>
    </div>

    <div class="contact">
      <p class="contact__name">Daniel Porter Jr.</p>
      <p class="contact__role">Project Manager</p>
      <ul class="contact__list">
        <li class="contact__item">
          <svg class="contact__icon" viewBox="0 0 24 24" aria-hidden="true">
            <path fill="var(--brand-green)" d="M6.6 10.8c1.4 2.8 3.8 5.1 6.6 6.6l2.2-2.2c.3-.3.7-.4 1-.2 1.1.4 2.3.6 3.6.6.6 0 1 .4 1 1V20c0 .6-.4 1-1 1C10.6 21 3 13.4 3 4c0-.6.4-1 1-1h3.5c.6 0 1 .4 1 1 0 1.3.2 2.5.6 3.6.1.3 0 .7-.2 1z"/>
          </svg>
          <span>555-014-0250 ext.809</span>
        </li>
        <li class="contact__item">
          <svg class="contact__icon" viewBox="0 0 24 24" aria-hidden="true">
            <path fill="var(--brand-green)" d="M7 3h10v5H7zM4 9h16a2 2 0 0 1 2 2v6h-4v4H6v-4H2v-6a2 2 0 0 1 2-2zm4 7v3h8v-3z"/>
          </svg>
          <span>555-018-1271</span>
        </li>
        <li class="contact__item">
          <svg class="contact__icon" viewBox="0 0 24 24" aria-hidden="true">
            <path fill="var(--brand-green)" d="M2 5h20v14H2zm2 2v.5l8 5.5 8-5.5V7l-8 5.5z"/>
          </svg>
          <span>dan@GreenHollowLandscapes.com</span>
        </li>
      </ul>
    </div>
  </section>

</main>
</body>
</html>
```